Blind Rivet Product catalogue

Need a design in wordpress with a productcatalogue where i present all products. This is a B2B business. The products is Blindrivets and Blindrivet nuts and accessories to this. I only want the basic information and also technical specification.

This is a subcompany to my existing company k7.m3.se but specializing in a subcategory

Businesses using blind rivet technology.

Industrial

Sans Serif

Must have
• Three different categories for the products; Blind Rivets - Blind Rivet Nut - Riveting Tools
Nice to have
• Possible to ad login for more information of the different sizes

```html
<!DOCTYPE html>
<html lang="en">
<head>
<meta charset="utf-8">
<title>K7M3 – Blind Rivet</title>
<link href="https://fonts.googleapis.com/css2?family=Exo+2:wght@400;600;700;800&family=Roboto:wght@400;500;700&display=swap" rel="stylesheet">
<style>
:root{
  --red:#e3001b;
  --green:#5aab3a;
  --black:#000;
  --dark:#1b1b1b;
  --darker:#141414;
  --nav:#4b4b4b;
  --text:#333;
  --muted:#555;
  --light:#f1f1f1;
  --card:#f6f6f6;
  --white:#fff;
}
*{margin:0;padding:0;box-sizing:border-box}
html,body{width:1200px;height:3598px;overflow:hidden}
body{position:relative;font-family:"Roboto",sans-serif;color:var(--text);background:var(--white)}
.abs{position:absolute}
.head{font-family:"Exo 2",sans-serif}
.btn{position:absolute;background:var(--red);color:var(--white);font-family:"Exo 2",sans-serif;font-weight:700;text-transform:uppercase;display:flex;align-items:center;justify-content:center;border-radius:3px}
.rule{position:absolute;height:3px;background:var(--red)}

/* header */
.topbar{left:0;top:0;width:1200px;height:119px;background:var(--black)}
.logo{left:144px;top:34px;color:var(--white)}
.logo-name{font-family:"Exo 2",sans-serif;font-weight:700;font-size:28px;letter-spacing:2px;display:flex;align-items:center;gap:8px}
.logo-name i{display:block;width:14px;height:14px;background:var(--green)}
.logo-tag{font-size:10px;color:#aaa;margin-top:2px}
.toll{left:445px;top:38px;color:var(--white)}
.toll small{font-size:13px;display:block}
.toll b{font-family:"Exo 2",sans-serif;font-size:23px;font-weight:600}
.search{left:645px;top:44px;width:233px;height:32px;background:var(--white);border-radius:16px;font-size:11px;color:#888;padding:10px 17px}
.login{left:898px;top:44px;width:105px;height:32px;border-radius:16px;font-size:13px}
.navbar{left:0;top:119px;width:1200px;height:49px;background:var(--nav)}
.nav{left:154px;top:134px;display:flex;gap:0;color:var(--white);font-family:"Exo 2",sans-serif;font-weight:700;font-size:15px}
.nav span{position:absolute;white-space:nowrap}

/* hero */
.hero{left:0;top:168px;width:1200px;height:551px;background:linear-gradient(90deg,#8a5c48 0%,#b07a5e 35%,#a35040 60%,#5e2e2a 100%)}
.hero-title{left:144px;top:358px;color:var(--white);font-family:"Exo 2",sans-serif;font-weight:800;font-size:48px;line-height:48px}
.dot{position:absolute;width:17px;height:17px;border-radius:50%;border:2px solid var(--white);top:661px}

/* welcome */
.welcome-h{left:566px;top:808px;font-family:"Exo 2",sans-serif;font-size:28px;color:#222}
.welcome-h b{font-weight:800}
.welcome-p{left:566px;top:890px;width:495px;font-size:14px;line-height:25.6px;color:#444}

/* products */
.green{left:0;top:1218px;width:1200px;height:428px;background:var(--green)}
.sec-title{width:1200px;left:0;text-align:center;font-family:"Exo 2",sans-serif;font-weight:700}
.card{position:absolute;top:1443px;width:284px;height:353px;background:var(--card);box-shadow:0 2px 6px rgba(0,0,0,.15)}
.card .img{height:203px;background:var(--white);display:flex;align-items:center;justify-content:center}
.card .img div{width:170px;height:140px;border-radius:8px}
.card h3{font-family:"Exo 2",sans-serif;font-weight:600;font-size:18px;text-align:center;margin-top:27px;color:#222}
.card p{font-size:14px;line-height:21px;text-align:center;color:#555;margin:14px 24px 0}

/* partners */
.badge{position:absolute;top:2200px;width:176px;height:80px;background:var(--white);border:2px solid #ddd;display:flex;align-items:center;justify-content:center}
.badge i{display:block;width:110px;height:26px;background:#c9c9c9;border-radius:3px}

/* blog */
.post{position:absolute;top:2597px;width:287px}
.post .img{height:183px}
.date{position:absolute;left:0;top:210px;width:32px;height:44px;font-size:9px;font-weight:700;color:var(--white);text-align:center}
.date span{display:block;height:22px;line-height:22px}
.post h4{margin-left:50px;margin-top:25px;font-family:"Exo 2",sans-serif;font-weight:700;font-size:15px;line-height:18px;color:#222}
.post p{margin-left:50px;margin-top:10px;font-size:13.5px;line-height:16.5px;color:#444}
.post .more{margin-left:50px;margin-top:16px;width:116px;height:34px;border:2px solid #222;font-family:"Exo 2",sans-serif;font-weight:700;font-size:12px;display:flex;align-items:center;justify-content:center;border-radius:2px}

/* footer */
.footer{left:0;top:3073px;width:1200px;height:362px;background:var(--dark)}
.bottom{left:0;top:3435px;width:1200px;height:163px;background:var(--darker)}
.f-title{font-family:"Exo 2",sans-serif;font-weight:600;font-size:23px;color:var(--white)}
.f-text{color:#ddd;font-size:14px;line-height:21px;letter-spacing:.4px}
.links{color:#ddd;font-size:14px;line-height:25.5px}
.email{left:436px;top:3267px;width:302px;height:40px;background:var(--white);border-radius:20px;font-size:12px;color:#555;padding:13px 18px}
.social{position:absolute;top:3482px;width:25px;height:25px;border-radius:50%;border:1.5px solid #ddd}
</style>
</head>
<body>

<!-- Header -->
<div class="abs topbar"></div>
<div class="abs logo">
  <div class="logo-name"><i></i>K7M3</div>
  <div class="logo-tag">Fastening solutions</div>
</div>
<svg class="abs" style="left:400px;top:43px" width="34" height="34" viewBox="0 0 34 34">
  <circle cx="17" cy="17" r="17" fill="#e3001b"/>
  <path d="M11 9c1.5-1 3 0 3.8 1.8l.8 1.8c.4 1-.3 1.8-1 2.4 1 2.2 2.7 4 4.8 5 .6-.7 1.4-1.4 2.4-1l1.8.8c1.8.8 2.8 2.3 1.8 3.8-1.4 2-4 2.3-6.5 1-4-2-6.8-5-8.8-9-1.2-2.6-1-5 .9-6.6z" fill="#fff"/>
</svg>
<div class="abs toll"><small>Toll free :</small><b>+800 5510 2240</b></div>
<div class="abs search">Search here</div>
<svg class="abs" style="left:853px;top:53px" width="15" height="15" viewBox="0 0 15 15"><circle cx="6" cy="6" r="4.5" fill="none" stroke="#777" stroke-width="2"/><path d="M9.5 9.5l4 4" stroke="#777" stroke-width="2"/></svg>
<div class="btn login">Login</div>
<svg class="abs" style="left:1019px;top:40px" width="40" height="40" viewBox="0 0 40 40">
  <circle cx="18" cy="21" r="16" fill="none" stroke="#e3001b" stroke-width="2"/>
  <path d="M12 17h12l-1 10h-10z" fill="#e3001b"/><path d="M15 17a3 3 0 016 0" fill="none" stroke="#e3001b" stroke-width="2"/>
  <circle cx="31" cy="8" r="5.5" fill="#e3001b"/><text x="31" y="11" font-size="8" fill="#fff" text-anchor="middle" font-family="Roboto,sans-serif">2</text>
</svg>

<div class="abs navbar"></div>
<nav class="abs nav" style="left:0;top:134px">
  <span style="left:154px">HOME</span>
  <span style="left:234px">MARIN</span>
  <span style="left:318px">SCREW</span>
  <span style="left:410px">STICKS</span>
  <span style="left:495px">NUTS</span>
  <span style="left:570px">TRAYS</span>
  <span style="left:650px">SCREW PIN</span>
  <span style="left:767px">OTHER ATTACHMENT</span>
  <span style="left:955px">CONTACT US</span>
</nav>
<div class="abs" style="left:154px;top:164px;width:45px;height:3px;background:#fff"></div>

<!-- Hero -->
<div class="abs hero" role="img" aria-label="Photo of a smiling worker in a red hard hat and plaid shirt holding a cordless rivet tool in a workshop"></div>
<h1 class="abs hero-title">BLINDRIVET NUTS<br>AND ACCESSORIES</h1>
<div class="btn" style="left:144px;top:480px;width:169px;height:42px;font-size:17px">Learn More</div>
<span class="dot" style="left:566px;background:var(--red)"></span>
<span class="dot" style="left:594px"></span>
<span class="dot" style="left:619px"></span>

<!-- Welcome -->
<svg class="abs" style="left:163px;top:785px" width="356" height="356" viewBox="0 0 356 356">
  <circle cx="178" cy="178" r="176" fill="#fff" stroke="#111" stroke-width="2"/>
  <circle cx="178" cy="178" r="166" fill="#6e6e6e" role="img" aria-label="Black and white photo of a rope tied to a steel snap hook"/>
</svg>
<h2 class="abs welcome-h">WELCOME TO <b>BLIND RIVET</b></h2>
<div class="rule" style="left:566px;top:863px;width:63px"></div>
<p class="abs welcome-p">Sed ut perspiciatis unde omnis iste natus error sit voluptatem accuntium doloremque laudantium, totam rem aperiam, eaque ipsa quae ab illo inore veritatis et quasi architecto beatae vitae dicta sunt explicabo. Nemo enim ipsam voluptatem quia voluptas sit aspernatur aut odit aut fugit, sed quia consequuntur magni dolores eos qui ratione voluptatem sequi nesciunt. Neque porro quisquam est, qui dolorem ipsum quia dolor</p>
<div class="btn" style="left:566px;top:1067px;width:137px;height:36px;font-size:14px">Learn More</div>

<!-- Products -->
<div class="abs green"></div>
<h2 class="abs sec-title" style="top:1305px;font-size:40px;color:var(--white)">OUR PRODUCTS</h2>
<div class="abs" style="left:563px;top:1372px;width:74px;height:3px;background:#fff"></div>

<div class="card" style="left:144px">
  <div class="img"><div role="img" aria-label="Product photo of a knurled steel blind rivet nut" style="background:linear-gradient(135deg,#eee,#9a9a9a)"></div></div>
  <h3>Blind Rivet Nut</h3>
  <p>Sed ut perspiciatis unde omnis iste natus sit voluptatem accusantium doloremque laudantium</p>
</div>
<div class="card" style="left:458px">
  <div class="img"><div role="img" aria-label="Product photo of a steel blind rivet with mandrel" style="background:linear-gradient(135deg,#f0f0f0,#a5a5a5)"></div></div>
  <h3>Blind Rivets</h3>
  <p>Sed ut perspiciatis unde omnis iste natus sit voluptatem accusantium doloremque laudantium</p>
</div>
<div class="card" style="left:771px">
  <div class="img"><div role="img" aria-label="Product photo of a cordless battery riveting tool" style="background:linear-gradient(135deg,#ddd,#2a2a2a)"></div></div>
  <h3>Riveting Tools</h3>
  <p>Sed ut perspiciatis unde omnis iste natus sit voluptatem accusantium doloremque laudantium</p>
</div>
<div class="btn" style="left:491px;top:1855px;width:217px;height:42px;font-size:14px">View More Products</div>

<!-- Partners -->
<svg class="abs" style="left:0;top:1963px" width="1200" height="490" viewBox="0 0 1200 490">
  <path d="M0 0L600 53L1200 0V490L600 434L0 490z" fill="#f1f1f1"/>
</svg>
<h2 class="abs sec-title" style="top:2092px;font-size:38px;color:#333">OUR PARTNERS</h2>
<div class="rule" style="left:571px;top:2157px;width:58px"></div>
<svg class="abs" style="left:86px;top:2222px" width="20" height="36" viewBox="0 0 20 36"><path d="M17 2L3 18l14 16" fill="none" stroke="#aaa" stroke-width="2"/></svg>
<div class="badge" style="left:132px"><i></i></div>
<div class="badge" style="left:322px"><i></i></div>
<div class="badge" style="left:513px"><i></i></div>
<div class="badge" style="left:703px"><i></i></div>
<div class="badge" style="left:893px"><i></i></div>
<svg class="abs" style="left:1088px;top:2222px" width="20" height="36" viewBox="0 0 20 36"><path d="M3 2l14 16L3 34" fill="none" stroke="#aaa" stroke-width="2"/></svg>

<!-- Blog -->
<h2 class="abs sec-title" style="top:2475px;font-size:38px;color:#333">LATEST BLOG</h2>
<div class="rule" style="left:563px;top:2539px;width:74px"></div>

<div class="post" style="left:135px">
  <div class="img" role="img" aria-label="Photo of a sailing boat deck and rigging on the open sea" style="background:linear-gradient(180deg,#b9cde0,#2c4c7a 60%,#e8e8e8)"></div>
  <div class="date"><span style="background:var(--green)">JAN</span><span style="background:#111">2020</span></div>
  <h4>Nemo Enim Ipsam Voluptatem Quia Voluptas Sit</h4>
  <p>Lorem ipsum dolor sit amet, coetur adipiscing elit, sed do eiusmod tempor incididunt ut labore et dolore magna aliqua. Ut enim ad minim veniam, quis nostrud</p>
  <div class="more">LEARN MORE</div>
</div>
<div class="post" style="left:455px">
  <div class="img" role="img" aria-label="Photo of a metal lathe machining a steel part" style="background:linear-gradient(135deg,#2f4a66,#8fa5b8 55%,#34465a)"></div>
  <div class="date"><span style="background:var(--green)">JAN</span><span style="background:#111">2020</span></div>
  <h4>Nemo Enim Ipsam Voluptatem Quia Voluptas Sit</h4>
  <p>Lorem ipsum dolor sit amet, coetur adipiscing elit, sed do eiusmod tempor incididunt ut labore et dolore magna aliqua. Ut enim ad minim veniam, quis nostrud</p>
  <div class="more">LEARN MORE</div>
</div>
<div class="post" style="left:775px">
  <div class="img" role="img" aria-label="Photo of hands tightening a brass fitting with an adjustable wrench" style="background:linear-gradient(135deg,#5a2a1a,#c28a5a 50%,#3a1c14)"></div>
  <div class="date"><span style="background:var(--green)">JAN</span><span style="background:#111">2020</span></div>
  <h4>Nemo Enim Ipsam Voluptatem Quia Voluptas Sit</h4>
  <p>Lorem ipsum dolor sit amet, coetur adipiscing elit, sed do eiusmod tempor incididunt ut labore et dolore magna aliqua. Ut enim ad minim veniam, quis nostrud</p>
  <div class="more">LEARN MORE</div>
</div>

<!-- Footer -->
<div class="abs footer"></div>
<div class="abs bottom"></div>

<h3 class="abs f-title" style="left:143px;top:3143px">CONTACT US</h3>
<svg class="abs" style="left:144px;top:3199px" width="16" height="22" viewBox="0 0 16 22"><path d="M8 1a7 7 0 017 7c0 5-7 13-7 13S1 13 1 8a7 7 0 017-7z" fill="none" stroke="#ddd" stroke-width="1.5"/><circle cx="8" cy="8" r="2.5" fill="none" stroke="#ddd" stroke-width="1.5"/></svg>
<div class="abs f-text" style="left:180px;top:3196px">K7M3<br>48 Harbour Lane Central<br>District Hong Kong</div>
<svg class="abs" style="left:144px;top:3279px" width="18" height="18" viewBox="0 0 18 18"><path d="M3 1.5l3 .5 1.5 3.5-2 1.5a10 10 0 005 5l1.5-2 3.5 1.5.5 3c-1 1.5-3 2-5 1A16 16 0 011.5 6.5c-1-2-.5-4 1.5-5z" fill="none" stroke="#ddd" stroke-width="1.3"/></svg>
<div class="abs f-text" style="left:180px;top:3279px">Phone : +852 30247716</div>
<svg class="abs" style="left:144px;top:3324px" width="20" height="14" viewBox="0 0 20 14"><rect x=".75" y=".75" width="18.5" height="12.5" fill="none" stroke="#ddd" stroke-width="1.3"/><path d="M1 1l9 7 9-7M1 13l6.5-6M19 13l-6.5-6" fill="none" stroke="#ddd" stroke-width="1.3"/></svg>
<div class="abs f-text" style="left:180px;top:3321px">Email : support@k7m3.se</div>

<h3 class="abs f-title" style="left:436px;top:3140px">SIGN UP TO RECEIVE EMAIL</h3>
<p class="abs f-text" style="left:436px;top:3198px;width:320px;font-size:13.5px;line-height:24px;letter-spacing:0">Excepteur sint occaecat cupidatat non proident, sunt in culpa qui Nemo enim ipsam voluptatem</p>
<div class="abs email">Enter Email</div>
<div class="btn" style="left:436px;top:3325px;width:150px;height:39px;border-radius:20px;font-size:14px">Subscribe</div>

<h3 class="abs f-title" style="left:810px;top:3140px">QUICK LINKS</h3>
<div class="abs links" style="left:814px;top:3196px">Marin<br>Screw<br>sticks<br>nuts<br>trays<br>Screw Pin</div>
<div class="abs links" style="left:941px;top:3196px">Other attachment<br>Contact Us<br>About us<br>Sitemap</div>

<span class="social" style="left:541px"></span>
<span class="social" style="left:572px"></span>
<span class="social" style="left:603px"></span>
<span class="social" style="left:634px"></span>
<p class="abs" style="left:0;top:3531px;width:1200px;text-align:center;color:#ddd;font-size:15px">Copyright © K7M3 2020. All rights reserved. | Privacy Policy</p>

</body>
</html>
```